Web Design Project

Hi, we need a new and professional design for our company "partnertradecircuitry". The website should communicate business but with a friendly and professional touch.

You can use the following categories for the menu;

Home - customer groups - products - voucher system- contact

Give it your best,

Regards,
Oswin

Industry/Entity Type

Business

```html
<!DOCTYPE html>
<html lang="en">
<head>
<meta charset="utf-8">
<title>partnertradecircuitry – Products</title>
<link rel="stylesheet" href="https://fonts.googleapis.com/css2?family=Arimo:wght@400;700&display=swap">
<style>
  :root {
    --ink: #000000;
    --paper: #ffffff;
    --accent: #1f8a1f;
    --accent-dark: #0d4a0d;
    --font: "Arimo", Arial, sans-serif;
  }
  * { box-sizing: border-box; margin: 0; padding: 0; }
  html, body { width: 1200px; height: 900px; overflow: hidden; background: var(--ink); }
  .page {
    position: relative; width: 1200px; height: 900px;
    background: var(--ink); color: var(--paper); font-family: var(--font);
    overflow: hidden;
  }
  .decor { position: absolute; inset: 0; width: 1200px; height: 900px; pointer-events: none; z-index: 1; }

  .brand {
    position: absolute; left: 30px; top: 128px;
    display: flex; align-items: center; gap: 10px;
    font-size: 24px; font-weight: 400; color: var(--paper);
  }
  .brand__square { width: 14px; height: 14px; background: var(--paper); }

  .main-nav { position: absolute; left: 10px; top: 450px; width: 170px; z-index: 2; }
  .main-nav__item {
    position: relative; display: block; height: 54px; margin-bottom: 14px;
    color: var(--paper); text-decoration: none; font-size: 20px;
  }
  .main-nav__swoosh { position: absolute; left: 0; top: 0; width: 170px; height: 54px; }
  .main-nav__label {
    position: absolute; left: 0; top: 0; width: 110px; height: 54px;
    display: flex; align-items: center; justify-content: center;
    text-align: center; line-height: 1.05;
  }
  .main-nav__label--small { font-size: 18px; }

  .product-grid {
    position: absolute; left: 316px; top: 41px;
    display: grid; grid-template-columns: 361px 361px; column-gap: 46px; row-gap: 14px;
    z-index: 2;
  }
  .product-card {
    position: relative; height: 184px; border-radius: 10px;
    border: 3px solid var(--accent-dark);
    border-top-color: var(--accent); border-bottom-color: var(--accent);
    background: var(--ink);
  }
  .product-card__image {
    position: absolute; left: 20px; top: 20px; width: 136px; height: 137px;
    background: var(--paper); color: var(--ink);
    display: flex; align-items: center; justify-content: center; text-align: center;
    font-size: 20px; font-weight: 700; line-height: 1.5;
  }
  .product-card__body {
    position: absolute; left: 170px; top: 20px; width: 180px;
    font-size: 20px; font-weight: 700; line-height: 26px;
  }
  .product-card__more {
    position: absolute; right: 30px; bottom: 8px;
    font-size: 19px; font-weight: 700; color: var(--paper); text-decoration: none;
  }

  .corner-brand {
    position: absolute; right: 22px; bottom: 30px; z-index: 3;
    display: flex; align-items: center; gap: 8px;
    font-size: 20px; font-weight: 400; color: var(--ink);
  }
  .corner-brand__square { width: 12px; height: 12px; background: var(--ink); }

  .copyright {
    position: absolute; left: 293px; top: 873px; z-index: 2;
    font-size: 14px; font-weight: 700; color: var(--paper);
  }
</style>
</head>
<body>
<div class="page">
  <svg class="decor" viewBox="0 0 1200 900" aria-hidden="true">
    <path d="M0,304 C170,300 255,560 268,900 L258,900 C244,580 160,322 0,316 Z" fill="var(--paper)"/>
    <path d="M527,900 C650,862 800,805 900,758 C1040,692 1140,612 1200,504 L1200,900 Z" fill="var(--paper)"/>
  </svg>

  <div class="brand"><span class="brand__square"></span>partnertradecircuitry</div>

  <nav class="main-nav">
    <a class="main-nav__item" href="#">
      <svg class="main-nav__swoosh" viewBox="0 0 170 54"><path d="M8,50 C90,54 158,40 158,24 C158,10 120,4 80,5 C125,9 148,16 147,26 C145,40 90,48 8,50 Z" fill="var(--paper)"/></svg>
      <span class="main-nav__label">Home</span>
    </a>
    <a class="main-nav__item" href="#">
      <svg class="main-nav__swoosh" viewBox="0 0 170 54"><path d="M8,50 C90,54 158,40 158,24 C158,10 120,4 80,5 C125,9 148,16 147,26 C145,40 90,48 8,50 Z" fill="var(--paper)"/></svg>
      <span class="main-nav__label main-nav__label--small">Customer<br>&nbsp;&nbsp;&nbsp;Groups</span>
    </a>
    <a class="main-nav__item" href="#">
      <svg class="main-nav__swoosh" viewBox="0 0 170 54"><path d="M8,50 C90,54 158,40 158,24 C158,10 120,4 80,5 C125,9 148,16 147,26 C145,40 90,48 8,50 Z" fill="var(--accent)"/></svg>
      <span class="main-nav__label">Products</span>
    </a>
    <a class="main-nav__item" href="#">
      <svg class="main-nav__swoosh" viewBox="0 0 170 54"><path d="M8,50 C90,54 158,40 158,24 C158,10 120,4 80,5 C125,9 148,16 147,26 C145,40 90,48 8,50 Z" fill="var(--paper)"/></svg>
      <span class="main-nav__label main-nav__label--small">Voucher<br>&nbsp;&nbsp;&nbsp;System</span>
    </a>
    <a class="main-nav__item" href="#">
      <svg class="main-nav__swoosh" viewBox="0 0 170 54"><path d="M8,50 C90,54 158,40 158,24 C158,10 120,4 80,5 C125,9 148,16 147,26 C145,40 90,48 8,50 Z" fill="var(--paper)"/></svg>
      <span class="main-nav__label">Contact</span>
    </a>
  </nav>

  <main class="product-grid">
    <article class="product-card"><div class="product-card__image" role="img" aria-label="Product photo">Product<br>Image</div><div class="product-card__body">Product Title<br>$cost<br>breif description here. Not much space</div><a class="product-card__more" href="#">more</a></article>
    <article class="product-card"><div class="product-card__image" role="img" aria-label="Product photo">Product<br>Image</div><div class="product-card__body">Product Title<br>$cost<br>breif description here. Not much space</div><a class="product-card__more" href="#">more</a></article>
    <article class="product-card"><div class="product-card__image" role="img" aria-label="Product photo">Product<br>Image</div><div class="product-card__body">Product Title<br>$cost<br>breif description here. Not much space</div><a class="product-card__more" href="#">more</a></article>
    <article class="product-card"><div class="product-card__image" role="img" aria-label="Product photo">Product<br>Image</div><div class="product-card__body">Product Title<br>$cost<br>breif description here. Not much space</div><a class="product-card__more" href="#">more</a></article>
    <article class="product-card"><div class="product-card__image" role="img" aria-label="Product photo">Product<br>Image</div><div class="product-card__body">Product Title<br>$cost<br>breif description here. Not much space</div><a class="product-card__more" href="#">more</a></article>
    <article class="product-card"><div class="product-card__image" role="img" aria-label="Product photo">Product<br>Image</div><div class="product-card__body">Product Title<br>$cost<br>breif description here. Not much space</div><a class="product-card__more" href="#">more</a></article>
    <article class="product-card"><div class="product-card__image" role="img" aria-label="Product photo">Product<br>Image</div><div class="product-card__body">Product Title<br>$cost<br>breif description here. Not much space</div><a class="product-card__more" href="#">more</a></article>
    <article class="product-card"><div class="product-card__image" role="img" aria-label="Product photo">Product<br>Image</div><div class="product-card__body">Product Title<br>$cost<br>breif description here. Not much space</div><a class="product-card__more" href="#">more</a></article>
  </main>

  <div class="corner-brand"><span class="corner-brand__square"></span>partnertradecircuitry</div>

  <footer class="copyright">Copyright 2013</footer>
</div>
</body>
</html>
```